Call Center In Need of Website Design

We are a call center that provides inbound and outbound calling & marketing services for eCommerce store. We would like to see a fun, creative, playful design that is simple.

Here are some sample design sites we like;
- https://www.velmoreline.com/
- https://pindrask.io/
- https://www.glimbertic.com/live-chat-software/
- https://www.zavrolin.com/

Here are some competitor sites;
- https://www.ostrevaglinks.com/
- https://www.helpkestrel.com/

I have attached website content for your use.

Target Market(s)

eCommerce

Coding

Coded - Design and coding required

Number of Pages Required

5+ page

Font styles to use
Sans Serif

Colors

Designer to choose colors to be used in the design.

Requirements
Must have
• Must have designs for the following 5 separate pages;
• 1. Home (landing)
• - This will be were the design style really needs to show.
• - Just needs to touch on key services
• - CTA
• 2. About Us
• - Basic page for about me paragraph
• 3. Services
• - List of services with icons
• - Click on service type to expand details or hover over service icon to view popup bubble with details about that service
• 4. Pricing
• - Option to bundle 1(one) digital service plan and 1(one) call center service plan
• - Bundling adds 10% monthly discount to over all price
• - Customer does NOT have to bundle
• - FAQ
• 5. Contact Us
• - Include a capture form (name, company name, email, phone, message)
• - Contact info
• - Business hours
• When customer purchases their desired plan, then they are taken to a page where they must schedule a call with an account rep.
Nice to have
• home page animations
Should not have
• All information on Home/Landing page.

```html
<!DOCTYPE html>
<html lang="en">
<head>
<meta charset="utf-8">
<title>Orbitalle — Personal Customer Service</title>
<link href="https://fonts.googleapis.com/css2?family=Mulish:wght@400;600;700;800&family=Open+Sans:ital,wght@0,400;0,600;0,700;1,700&display=swap" rel="stylesheet">
<style>
  :root{
    --teal:#5cc3a8;
    --teal-deep:#4bb897;
    --teal-soft:#7fd3bc;
    --mint:#b8efdf;
    --ink:#1e1e1e;
    --body:#555;
    --white:#ffffff;
  }
  *{box-sizing:border-box;margin:0;padding:0}
  html,body{width:1200px;height:2773px;overflow:hidden;background:var(--white)}
  body{position:relative;font-family:"Open Sans",sans-serif;color:var(--ink)}
  h1,h2,h3,.brand{font-family:"Mulish",sans-serif}

  /* hero */
  .hero-bg{position:absolute;left:0;top:0;width:1200px;height:700px}
  .brand{position:absolute;display:flex;align-items:center;gap:14px;font-size:28px;font-weight:600;letter-spacing:3.5px;color:var(--white);white-space:nowrap}
  .brand .dot{width:26px;height:26px;border-radius:50%;background:var(--white)}
  .nav-item{position:absolute;top:39px;font-size:11px;font-weight:700;color:var(--white);white-space:nowrap;line-height:14px}
  .btn-outline{position:absolute;left:934px;top:28px;width:103px;height:37px;border:2px solid var(--white);color:var(--white);font-size:11px;font-weight:700;display:flex;align-items:center;justify-content:center;white-space:nowrap}
  .hero-figure{position:absolute;left:37px;top:139px;width:638px;height:481px;border-radius:40% 30% 8px 8px;background:linear-gradient(160deg,#3a3f4a 0%,#50555f 55%,#a85a32 100%);opacity:.9}
  .hero-title{position:absolute;left:487px;top:200px;width:580px;font-size:46px;line-height:52px;font-weight:700;color:var(--white)}
  .hero-sub{position:absolute;left:490px;top:328px;font-size:12px;letter-spacing:2.6px;font-weight:700;color:var(--white);white-space:nowrap}
  .btn-white{position:absolute;left:488px;top:377px;width:126px;height:50px;background:var(--white);color:var(--ink);font-size:14px;font-weight:600;display:flex;align-items:center;justify-content:center}
  .scroll-pill{position:absolute;left:588px;top:623px;width:26px;height:54px;border-radius:13px;background:var(--white);box-shadow:0 2px 8px rgba(0,0,0,.12)}
  .scroll-pill::after{content:"";position:absolute;left:12px;top:17px;width:2px;height:20px;background:var(--teal)}

  .section-title{position:absolute;font-size:26px;font-weight:600;color:var(--ink);text-decoration:underline;text-underline-offset:6px;text-decoration-thickness:2px;white-space:nowrap}
  .copy{position:absolute;font-size:11.5px;line-height:22.5px;color:var(--body)}

  /* services */
  .link-more{position:absolute;left:161px;top:944px;font-size:12px;font-weight:700;text-decoration:underline;color:var(--ink)}
  .service-card{position:absolute;top:769px;width:190px;height:214px;border-radius:6px;box-shadow:0 6px 18px rgba(0,0,0,.15);overflow:hidden}
  .service-card.is-active{left:599px;background:var(--teal-deep);color:var(--white);font-size:10.5px;line-height:19.5px;text-align:center;padding:30px 16px 0}
  .service-card.is-plain{left:819px;background:var(--white);padding:22px}
  .service-art{width:146px;height:170px;border-radius:4px;background:linear-gradient(160deg,#dfe6ee,#b7c4d2)}
  .service-label{position:absolute;top:995px;width:190px;text-align:center;font-size:14px;font-weight:600}

  /* what we do */
  .people-art{position:absolute;left:24px;top:1198px;width:471px;height:244px;background:linear-gradient(90deg,#f3b4a6 0%,#c8cfdc 50%,#2a2f4a 100%);border-radius:6px;opacity:.85}
  .wwd-sub{position:absolute;left:582px;top:1262px;width:370px;font-size:14px;line-height:26px;font-style:italic;font-weight:700;color:var(--ink)}
  .btn-teal{position:absolute;background:var(--teal-deep);color:var(--white);font-weight:700;display:flex;align-items:center;justify-content:center;white-space:nowrap}

  /* faq */
  .faq{position:absolute;top:1870px}
  .faq-num{position:absolute;left:-54px;top:3px;width:40px;height:27px}
  .faq h3{font-family:"Open Sans",sans-serif;font-size:13px;font-weight:700;margin-bottom:6px;white-space:nowrap}
  .faq p{font-size:11px;line-height:20.5px;color:var(--body)}
  .faq .btn-teal{position:static;width:82px;height:30px;font-size:10.5px;margin-top:10px}
  .dots{position:absolute;display:flex;gap:6px}
  .dots i{width:6px;height:6px;border-radius:50%;background:var(--ink)}
  .dots i.on{background:var(--teal)}

  /* clients */
  .clients{position:absolute;left:0;top:2075px;width:1200px;height:560px;background:linear-gradient(160deg,#a8ecd8,#c5f3e6 50%,#abebd8)}
  .quote-mark{position:absolute;left:390px;top:2282px;width:60px;height:44px}
  .review{position:absolute;left:383px;top:2302px;width:427px;height:231px;background:var(--white);text-align:center;padding-top:56px}
  .avatar{position:absolute;left:564px;top:2271px;width:64px;height:64px;border-radius:50%;background:linear-gradient(#cfd4da,#8c96a1);border:3px solid var(--white)}
  .review h3{font-family:"Open Sans",sans-serif;font-size:13px;font-weight:700}
  .review .date{font-size:10px;font-weight:700;color:#444;margin-top:3px}
  .review p{font-size:10.5px;line-height:20.5px;color:var(--body);width:380px;margin:18px auto 0}
  .review .learn{display:inline-block;margin-top:9px;font-size:9px;font-weight:700;letter-spacing:1px;color:var(--teal-deep);text-decoration:underline}
  .arrow{position:absolute;top:2414px}

  /* footer */
  .footer-head{position:absolute;top:2675px;font-size:14px;font-weight:700}
  .footer-text{position:absolute;font-size:11px;line-height:20px;color:#444;white-space:nowrap}
  .social{position:absolute;top:2712px;width:24px;height:24px;border:1.5px solid #555;border-radius:50%}
</style>
</head>
<body>

<svg class="hero-bg" viewBox="0 0 1200 700" aria-hidden="true">
  <path d="M0 0H1200V648C1060 618 930 650 760 660C560 672 380 650 220 600C120 568 50 530 0 492Z" fill="var(--teal)"/>
  <rect x="-20" y="40" width="110" height="380" rx="10" fill="#6fd0b6" opacity=".55"/>
  <rect x="330" y="115" width="90" height="85" fill="#79d6bd" opacity=".6"/>
  <rect x="1015" y="105" width="80" height="80" fill="#7ad7bf" opacity=".55"/>
  <rect x="1050" y="140" width="80" height="80" fill="#86dcc5" opacity=".5"/>
  <rect x="1080" y="350" width="60" height="60" fill="#6fd0b6" opacity=".7" transform="rotate(45 1110 380)"/>
  <rect x="1072" y="342" width="76" height="76" fill="none" stroke="#fff" stroke-dasharray="3 4" opacity=".6" transform="rotate(45 1110 380)"/>
  <rect x="780" y="495" width="282" height="160" rx="8" fill="none" stroke="#fff" stroke-dasharray="3 4" opacity=".6"/>
  <rect x="750" y="530" width="235" height="140" rx="8" fill="#4eb797" opacity=".6"/>
</svg>

<div class="brand" style="left:161px;top:30px"><span class="dot"></span>ORBITALLE</div>
<nav>
  <span class="nav-item" style="left:484px">Home</span>
  <span class="nav-item" style="left:533px">:</span>
  <span class="nav-item" style="left:553px">About Us</span>
  <span class="nav-item" style="left:619px">:</span>
  <span class="nav-item" style="left:640px">Services</span>
  <span class="nav-item" style="left:699px">:</span>
  <span class="nav-item" style="left:719px">Pricing</span>
  <span class="nav-item" style="left:774px">:</span>
  <span class="nav-item" style="left:795px">Contact Us</span>
</nav>
<div class="btn-outline">GET STARTED</div>

<div class="hero-figure" role="img" aria-label="Illustration of a customer service agent with a headset working at a laptop"></div>
<h1 class="hero-title">Orbitalle is your personal customer service</h1>
<div class="hero-sub">ORBITALLE IS YOUR PERSONAL CUSTOMER SERVICE AND PRODUCT</div>
<div class="btn-white">Services</div>
<div class="scroll-pill"></div>

<!-- our services -->
<h2 class="section-title" style="left:161px;top:762px">Our Services</h2>
<p class="copy" style="left:161px;top:816px;width:372px">Orbitalle is your personal customer service and product research team. We love eCommerce, but we love seeing business owners succeed even more! That is exactly why we have developed the processes and technology to take care of the most over looked areas in eCommerce - Customer Service and Retention.</p>
<div class="link-more">View More Informtion</div>

<div class="service-card is-active">Orbitalle is your personal customer service and product research team. We love eCommerce, but we love seeing business owners succeed even more! We take care of the most over looked areas in eCommerce - Customer Service</div>
<div class="service-label" style="left:599px">Digital Services</div>
<div class="service-card is-plain"><div class="service-art" role="img" aria-label="Illustration of a call center agent at a desk workstation"></div></div>
<div class="service-label" style="left:819px">Call Center Services</div>

<!-- what we do -->
<div class="people-art" role="img" aria-label="Illustration of two support agents with headsets and chat bubbles"></div>
<h2 class="section-title" style="left:582px;top:1203px">What We Do</h2>
<div class="wwd-sub">ORBITALLE IS YOUR PERSONAL CUSTOMER SERVICE AND PRODUCT RESEARCH TEAM</div>
<p class="copy" style="left:582px;top:1333px;width:362px;line-height:22.2px">Orbitalle is your personal customer service and product research team. We love eCommerce, but we love seeing business owners succeed even more! That is exactly why we have developed the processes and technology to take care of the most over looked areas in eCommerce - Customer Service and Retention. Let Orbitalle handle your customers while you focus on growing your business.<br>Orbitalle originally started out as a generalized call center support company. Based in California, the founder quickly realized that there was a lack of support for eCommerce owners..</p>
<div class="btn-teal" style="left:582px;top:1562px;width:123px;height:47px;font-size:12px">Learn More</div>

<!-- faq -->
<h2 class="section-title" style="left:161px;top:1800px">Frequently Ask Question</h2>

<div class="faq" style="left:216px;width:165px">
  <svg class="faq-num" viewBox="0 0 40 27" aria-hidden="true"><path d="M7 14a13 11 0 1 0 5-9L1 7l6 3" fill="none" stroke="var(--teal)" stroke-width="1.5"/><text x="20" y="19" font-size="13" text-anchor="middle" fill="var(--teal)" font-family="Open Sans">1</text></svg>
  <h3>Is the free trial really free?</h3>
  <p>The free trial only relates to the "call-center" service packages! There is no hidden fine print or fees...</p>
  <div class="btn-teal">Learn More</div>
</div>
<div class="faq" style="left:516px;width:215px">
  <svg class="faq-num" viewBox="0 0 40 27" aria-hidden="true"><path d="M7 14a13 11 0 1 0 5-9L1 7l6 3" fill="none" stroke="var(--teal)" stroke-width="1.5"/><text x="20" y="19" font-size="13" text-anchor="middle" fill="var(--teal)" font-family="Open Sans">2</text></svg>
  <h3>Can I change my service plan?</h3>
  <p style="width:215px">Yes. This is the beauty oumonth-to-month answering service agreement. You arenever locked down to any given pkan..</p>
  <div class="btn-teal">Learn More</div>
</div>
<div class="faq" style="left:849px;width:195px">
  <svg class="faq-num" viewBox="0 0 40 27" aria-hidden="true"><path d="M7 14a13 11 0 1 0 5-9L1 7l6 3" fill="none" stroke="var(--teal)" stroke-width="1.5"/><text x="20" y="19" font-size="13" text-anchor="middle" fill="var(--teal)" font-family="Open Sans">3</text></svg>
  <h3>Do I have to sign a contract?</h3>
  <p style="width:190px">Nope. All our service plans are month-to-month answering service agreements.</p>
  <div class="btn-teal" style="margin-top:4px">Learn More</div>
</div>
<div class="dots" style="left:585px;top:2044px"><i></i><i></i><i class="on"></i></div>

<!-- clients -->
<section class="clients"></section>
<h2 class="section-title" style="left:0;width:1200px;text-align:center;top:2188px">Our Happy Clients</h2>
<svg class="quote-mark" viewBox="0 0 60 44" aria-hidden="true">
  <path d="M2 44V24C2 10 10 2 24 0v8c-7 2-10 6-10 12h10v24Z M34 44V24C34 10 42 2 56 0v8c-7 2-10 6-10 12h10v24Z" fill="var(--teal-deep)"/>
</svg>
<div class="review">
  <h3>Dara Quill</h3>
  <div class="date">10 July-2018</div>
  <p>Lorem Ipsum is simply dummy text of the printing and typesettingindustry. Lorem Ipsum has been the industry's standard dummy text ever since the 1500s, when an unknown printer...</p>
  <span class="learn">LEARN MORE</span>
</div>
<div class="avatar" role="img" aria-label="Client portrait photo"></div>
<svg class="arrow" style="left:278px" width="22" height="16" viewBox="0 0 22 16" aria-hidden="true"><path d="M21 8H2M8 2L2 8l6 6" fill="none" stroke="#111" stroke-width="2.2"/></svg>
<svg class="arrow" style="left:897px" width="22" height="16" viewBox="0 0 22 16" aria-hidden="true"><path d="M1 8h19M14 2l6 6-6 6" fill="none" stroke="#111" stroke-width="2.2"/></svg>
<div class="dots" style="left:588px;top:2570px"><i class="on"></i><i></i><i></i></div>

<!-- footer -->
<div class="brand" style="left:161px;top:2688px;font-size:26px;color:var(--ink)"><span class="dot" style="background:var(--teal)"></span>ORBITALLE</div>
<div class="footer-text" style="left:161px;top:2738px;font-size:10px">© Copyright 2018 Orbitalle.</div>

<div class="footer-head" style="left:473px">FIND US</div>
<div class="footer-text" style="left:473px;top:2705px">Orbitalle, Inc. 418 Larkhaven Rd.<br>Dunmere, CA 90210</div>

<div class="footer-head" style="left:710px">GET CONNECTED</div>
<div class="footer-text" style="left:710px;top:2705px">info@orbitalle.com<br>(800) 555-0147</div>

<div class="footer-head" style="left:943px">FOLLOW US</div>
<div class="social" style="left:944px"></div>
<div class="social" style="left:979px"></div>
<div class="social" style="left:1013px"></div>

</body>
</html>
```